UX Design for Analytics Web Application

http://velqoranthe.com/
We are tech & consulting company with analytics products (web applications), located at Rio de Janeiro, Brazil.

We are searching a partner do develop UX for our products, i.e, aesthetics, usability, HTML/CSS.

Currently we have a product suite and the goal is to make a pilot re-design project with one of our products.

The product of interest is interactive webapp that aims at data analysis, significantly different from blogs, e-commerce or landing pages.

We do have a software development team but we lack an UX & HTML expert. Currently we use Bootstrap templates but the results are insatisfatory.

So, the project scope is, to develop the arts (UX, aesthetics, etc) along with the code/mockup (HTML/CSS) for one of our product (3 pages).

This is a pilot project and there's potential to rehire for our other products. Code quality is of importance.

More details and specification can be found in attached files.

Target Market(s)

Executives, managers & consultants

Industry/Entity Type

It Company

Coding

Coded - Design and coding required

Number of Pages Required

3 page

Font styles to use
Sans Serif

Requirements
Must have
• (see attached files, prefer the pptx version))
• -Responsive
Nice to have
• (see attached files, prefer the pptx version)
Should not have
• -Avoid Green, Red and Yellow colors. They have a meaning of good, bad and average in our products.

```html
<!DOCTYPE html>
<html lang="en">
<head>
<meta charset="utf-8">
<title>Velqor – Process Dashboard</title>
<link rel="stylesheet" href="https://fonts.googleapis.com/css2?family=Montserrat:wght@300;400;500;600;700&display=swap">
<style>
:root{
  --ink:#222;
  --muted:#555;
  --accent:#2c5f9e;
  --primary:#1d4f86;
  --line:#dcdcdc;
  --hero:#ececec;
  --footer:#ebebeb;
  --dark:#3a3a3a;
  --white:#fff;
}
*{margin:0;padding:0;box-sizing:border-box}
html,body{width:1200px;height:2568px;overflow:hidden}
body{font-family:"Montserrat",sans-serif;color:var(--ink);background:var(--white);position:relative}

.topbar{position:absolute;left:0;top:0;width:1200px;height:103px;background:var(--white);box-shadow:0 2px 4px rgba(0,0,0,.12);z-index:2}
.menu-icon{position:absolute;left:133px;top:26px}
.brand{position:absolute;left:180px;top:28px;display:flex;align-items:center;gap:10px}
.brand-dot{width:34px;height:34px;border-radius:50%;background:var(--accent)}
.brand-name{font-size:36px;font-weight:600;color:#333;letter-spacing:1px}
.top-icon{position:absolute;top:34px}

.hero{position:absolute;left:0;top:103px;width:1200px;height:474px;background:linear-gradient(90deg,#e9e9e9,#f2f2f2 50%,#e7e7e7)}
.stat{position:absolute;display:flex;align-items:center}
.stat-circle{flex:none;width:142px;height:142px;border-radius:50%;background:var(--white);box-shadow:0 2px 8px rgba(0,0,0,.12);display:flex;align-items:center;justify-content:center;font-size:36px;font-weight:300;color:var(--accent)}
.stat-label{margin-left:24px;font-size:15px;color:var(--ink);line-height:28px;white-space:nowrap}
.stat-label strong{display:block;color:var(--primary);font-weight:700;font-size:14px;letter-spacing:.3px}

.feed{position:absolute;left:878px;top:159px;width:233px;height:358px;background:var(--white);box-shadow:0 1px 5px rgba(0,0,0,.15)}
.feed-head{height:34px;background:var(--dark);color:var(--white);font-size:13px;font-weight:600;display:flex;align-items:center;padding-left:12px;gap:8px;letter-spacing:.4px}
.feed-item{display:flex;gap:12px;padding:14px 0 0 16px;border-bottom:1px solid var(--line);margin-right:18px;height:104px}
.feed-item:last-child{border-bottom:none}
.avatar{flex:none;width:46px;height:46px;border-radius:50%;margin-top:12px}
.feed-date{font-size:9px;color:#555}
.feed-text{font-size:9px;line-height:13px;color:#333;margin-top:5px;width:134px}
.feed-name{font-size:8.5px;font-weight:600;margin-top:8px}

.process-grid{position:absolute;left:132px;top:630px;width:935px;display:grid;grid-template-columns:repeat(3,296px);column-gap:23px;row-gap:29px}
.process-card{height:258px;border:1px solid var(--line);background:radial-gradient(ellipse at center,#fff 65%,#f4f4f4 100%);text-align:center;padding-top:33px}
.process-title{font-size:21px;line-height:26px;font-weight:500;letter-spacing:.3px}
.process-price{font-size:26px;line-height:32px;color:var(--accent);margin-top:12px;font-weight:500}
.process-desc{font-size:13px;line-height:20px;color:#333;margin-top:26px}
.process-tag{display:inline-block;margin-top:29px;padding:5px 10px;font-size:12px;line-height:15px;background:#efefef;border:1px solid #ccc;color:#333}

.load-more{position:absolute;left:550px;top:2118px;width:101px;height:36px;border:1px solid #ccc;background:var(--white);font-family:inherit;font-size:11px;color:#444;letter-spacing:.3px}
.new-process{position:absolute;left:454px;top:2220px;width:296px;height:69px;background:var(--primary);color:var(--white);border:none;font-family:inherit;font-size:20px;font-weight:600;letter-spacing:.8px;display:flex;align-items:center;justify-content:center;gap:22px}

.footer{position:absolute;left:0;top:2357px;width:1200px;height:211px;background:var(--footer);text-align:center}
.footer .brand{position:absolute;left:522px;top:46px}
.footer .brand-dot{width:28px;height:28px}
.footer .brand-name{font-size:30px}
.footer-rule{position:absolute;left:476px;top:134px;width:252px;border-top:1px solid #c8c8c8}
.copyright{position:absolute;left:0;width:1200px;top:156px;font-size:12px;color:#333}
</style>
</head>
<body>
<header class="topbar">
  <svg class="menu-icon" width="26" height="22" viewBox="0 0 26 22"><g stroke="#333" stroke-width="2.4"><line x1="0" y1="2" x2="26" y2="2"/><line x1="0" y1="11" x2="26" y2="11"/><line x1="0" y1="20" x2="26" y2="20"/></g></svg>
  <div class="brand"><span class="brand-dot"></span><span class="brand-name">Velqor</span></div>
  <svg class="top-icon" style="left:880px" width="30" height="32" viewBox="0 0 30 32"><path d="M15 3a8 8 0 0 0-8 8v8l-4 5h24l-4-5v-8a8 8 0 0 0-8-8z M11 26a4 4 0 0 0 8 0" fill="none" stroke="#333" stroke-width="2"/></svg>
  <svg class="top-icon" style="left:956px" width="30" height="32" viewBox="0 0 30 32"><circle cx="15" cy="10" r="7" fill="none" stroke="#333" stroke-width="2"/><path d="M3 30c1-8 6-11 12-11s11 3 12 11z" fill="none" stroke="#333" stroke-width="2"/></svg>
  <svg class="top-icon" style="left:1038px" width="30" height="32" viewBox="0 0 30 30"><circle cx="15" cy="15" r="4.5" fill="none" stroke="#333" stroke-width="2"/><circle cx="15" cy="15" r="11" fill="none" stroke="#333" stroke-width="1.8" stroke-dasharray="5 3"/></svg>
</header>

<section class="hero">
  <div class="stat" style="left:91px;top:62px"><div class="stat-circle">125</div><div class="stat-label">Number of<strong>ACTIVE PROCESSES</strong></div></div>
  <div class="stat" style="left:462px;top:62px"><div class="stat-circle">75</div><div class="stat-label">Number of<strong>COMPLETED PROCESSES</strong></div></div>
  <div class="stat" style="left:91px;top:252px"><div class="stat-circle">89%</div><div class="stat-label"><strong>COMPLETION</strong></div></div>
  <div class="stat" style="left:462px;top:252px"><div class="stat-circle">$1500</div><div class="stat-label">Expenses of<strong>ALL PROCESSES</strong></div></div>
</section>

<aside class="feed">
  <div class="feed-head"><svg width="11" height="11" viewBox="0 0 11 11"><circle cx="1.6" cy="9.4" r="1.6" fill="#fff"/><path d="M0 4.5a6.5 6.5 0 0 1 6.5 6.5M0 1a10 10 0 0 1 10 10" fill="none" stroke="#fff" stroke-width="1.6"/></svg>ACTIVIY FEED</div>
  <div class="feed-item"><div class="avatar" role="img" aria-label="Profile photo of Dario" style="background:#8fa9a6"></div><div><div class="feed-date">30 MARCH,2017</div><div class="feed-text">There are many variations of passa of Lorem Ipsum.</div><div class="feed-name">DARIO</div></div></div>
  <div class="feed-item"><div class="avatar" role="img" aria-label="Profile photo of Tomas" style="background:#2f3a4a"></div><div><div class="feed-date">31 MARCH,2017</div><div class="feed-text">There are many variations of passa of Lorem Ipsum.</div><div class="feed-name">TOMAS</div></div></div>
  <div class="feed-item"><div class="avatar" role="img" aria-label="Profile photo of Leon Avery" style="background:#8a6a52"></div><div><div class="feed-date">01 APRIL,2017</div><div class="feed-text">There are many variations of passa of Lorem Ipsum.</div><div class="feed-name">LEON AVERY</div></div></div>
</aside>

<main class="process-grid">
  <article class="process-card"><h2 class="process-title">PROCESS #1</h2><p class="process-price">$25.00</p><p class="process-desc">There are many variations of<br>passa of Lorem Ipsum.</p><span class="process-tag">Executive Negotiation</span></article>
  <article class="process-card"><h2 class="process-title">PROCESS #2</h2><p class="process-price">$43.00</p><p class="process-desc">There are many variations of<br>passa of Lorem Ipsum.</p><span class="process-tag">Executive Negotiation</span></article>
  <article class="process-card"><h2 class="process-title">PROCESS #3</h2><p class="process-price">$18.00</p><p class="process-desc">There are many variations of<br>passa of Lorem Ipsum.</p><span class="process-tag">Executive Negotiation</span></article>
  <article class="process-card"><h2 class="process-title">PROCESS #4</h2><p class="process-price">$63.00</p><p class="process-desc">There are many variations of<br>passa of Lorem Ipsum.</p><span class="process-tag">Executive Negotiation</span></article>
  <article class="process-card"><h2 class="process-title">PROCESS #5</h2><p class="process-price">$56.00</p><p class="process-desc">There are many variations of<br>passa of Lorem Ipsum.</p><span class="process-tag">Executive Negotiation</span></article>
  <article class="process-card"><h2 class="process-title">PROCESS #6</h2><p class="process-price">$12.00</p><p class="process-desc">There are many variations of<br>passa of Lorem Ipsum.</p><span class="process-tag">Executive Negotiation</span></article>
  <article class="process-card"><h2 class="process-title">PROCESS #7</h2><p class="process-price">$63.00</p><p class="process-desc">There are many variations of<br>passa of Lorem Ipsum.</p><span class="process-tag">Executive Negotiation</span></article>
  <article class="process-card"><h2 class="process-title">PROCESS #8</h2><p class="process-price">$95.00</p><p class="process-desc">There are many variations of<br>passa of Lorem Ipsum.</p><span class="process-tag">Executive Negotiation</span></article>
  <article class="process-card"><h2 class="process-title">PROCESS #9</h2><p class="process-price">$34.00</p><p class="process-desc">There are many variations of<br>passa of Lorem Ipsum.</p><span class="process-tag">Executive Negotiation</span></article>
  <article class="process-card"><h2 class="process-title">PROCESS #10</h2><p class="process-price">$52.00</p><p class="process-desc">There are many variations of<br>passa of Lorem Ipsum.</p><span class="process-tag">Executive Negotiation</span></article>
  <article class="process-card"><h2 class="process-title">PROCESS #11</h2><p class="process-price">$35.00</p><p class="process-desc">There are many variations of<br>passa of Lorem Ipsum.</p><span class="process-tag">Executive Negotiation</span></article>
  <article class="process-card"><h2 class="process-title">PROCESS #12</h2><p class="process-price">$62.00</p><p class="process-desc">There are many variations of<br>passa of Lorem Ipsum.</p><span class="process-tag">Executive Negotiation</span></article>
  <article class="process-card"><h2 class="process-title">PROCESS #13</h2><p class="process-price">$78.00</p><p class="process-desc">There are many variations of<br>passa of Lorem Ipsum.</p><span class="process-tag">Executive Negotiation</span></article>
  <article class="process-card"><h2 class="process-title">PROCESS #14</h2><p class="process-price">$92.00</p><p class="process-desc">There are many variations of<br>passa of Lorem Ipsum.</p><span class="process-tag">Executive Negotiation</span></article>
  <article class="process-card"><h2 class="process-title">PROCESS #15</h2><p class="process-price">$32.00</p><p class="process-desc">There are many variations of<br>passa of Lorem Ipsum.</p><span class="process-tag">Executive Negotiation</span></article>
</main>

<button class="load-more">LOAD MORE</button>
<button class="new-process">NEW PROCESS <svg width="28" height="28" viewBox="0 0 28 28"><g stroke="#fff" stroke-width="2.4"><line x1="14" y1="0" x2="14" y2="28"/><line x1="0" y1="14" x2="28" y2="14"/></g></svg></button>

<footer class="footer">
  <div class="brand"><span class="brand-dot"></span><span class="brand-name">Velqor</span></div>
  <div class="footer-rule"></div>
  <p class="copyright">Copyrights @ 2017 All Rights Reserved</p>
</footer>
</body>
</html>
```